Varlomatch E-commerce Website Design

I'm looking into having my e-comm website built. We are an investment company that is investing in a private label focused on a rising sport category called Pickleball in EU market.

We will provide top quality material and acessories for players be ready to go to courts. We will have a range of: Rackets, Set of balls, Net, Lines, overgrip, water bottle, player bag.

As it´s a new sports category we would like to see an architecture that alows us to share some storytelling about the category, the brand and lead to purchase of our products.

We will position our self as an inclusive and fun brand that you can reach out to find more info about Pickleball Sport, buy your pickleball stuff and have fun. Its all about action and fun.

Target Market(s)

Europe Market

Industry/Entity Type

Pickleball (Sports)

Coding

Coded - Design and coding required

Number of Pages Required

1 page

Requirements
Must have
• E-commerce look and feel
Nice to have
• A bit of storytelling about the brand and specially the category (Pickleball).

```html
<!DOCTYPE html>
<html lang="en">
<head>
<meta charset="utf-8">
<title>Varlomatch – Pickleball Gear</title>
<link rel="stylesheet" href="https://fonts.googleapis.com/css2?family=Saira+Semi+Condensed:wght@400;500;600;700&family=Poppins:wght@400;500&display=swap">
<style>
:root{
  --yellow:#e8c52e;
  --blue:#0e9ad7;
  --navy:#22346e;
  --ink:#1c1c1c;
  --grey:#555;
  --light:#e9eef2;
  --band:#5a8ee0;
  --white:#fff;
  --black:#000;
}
*{box-sizing:border-box;margin:0;padding:0}
html,body{width:1200px;height:3871px;overflow:hidden}
body{position:relative;background:var(--white);font-family:"Saira Semi Condensed",sans-serif;color:var(--ink)}
.abs{position:absolute}
.btn{position:absolute;display:flex;align-items:center;justify-content:center;font-weight:600;color:var(--ink);background:var(--yellow)}
/* top bar */
.topbar{left:0;top:0;width:1200px;height:40px;background:var(--yellow);font-family:"Poppins",sans-serif;font-size:15px;display:flex;align-items:center;justify-content:center}
/* hero */
.hero{left:0;top:40px;width:1200px;height:552px;background:radial-gradient(ellipse at 60% 40%,#3b5da8 0%,#2a4688 55%,#1f3772 100%)}
.nav{left:110px;top:26px;display:flex;gap:48px;font-size:15px;color:var(--white)}
.nav .active{color:var(--yellow)}
.brand{display:flex;align-items:center;gap:8px;color:var(--white);font-weight:700;font-size:22px}
.brand .dot{width:22px;height:22px;border-radius:50%;background:var(--white)}
.search{left:701px;top:25px;width:260px;height:30px;border:1px solid var(--white);color:var(--white);font-size:14px;padding:5px 14px}
.iconbox{width:34px;height:30px;background:var(--yellow);display:flex;align-items:center;justify-content:center}
.hero-img{left:165px;top:103px;width:398px;height:398px;border-radius:40% 45% 30% 40%;background:linear-gradient(145deg,#8a8a8a,#3d3d3d 60%,#c9e540 90%);opacity:.85}
.hero h1{right:113px;top:163px;text-align:right;font-size:40px;line-height:50px;color:var(--white);font-weight:700;text-transform:uppercase}
.hero h1 span{color:var(--yellow)}
.hero p{right:113px;top:270px;width:420px;text-align:right;color:var(--white);font-size:14px;line-height:24px}
.arrow{width:22px;height:22px;border-radius:50%;background:var(--white);color:var(--navy);display:flex;align-items:center;justify-content:center;font-size:14px;font-weight:700}
/* section titles */
.title{font-weight:700;font-size:30px;text-transform:uppercase}
.title span{color:var(--blue)}
/* product cards */
.card{top:713px;width:231px;height:383px;background:var(--white);box-shadow:0 0 8px rgba(0,0,0,.15)}
.card.focus{border:1px solid #666}
.card .media{position:absolute;left:6px;top:6px;width:219px;height:189px}
.tag{position:absolute;right:18px;top:20px;font-size:11px;color:var(--white);padding:1px 8px;font-family:"Poppins",sans-serif}
.card .price{position:absolute;left:18px;top:200px;color:var(--blue);font-size:21px;font-weight:600}
.card .name{position:absolute;left:18px;top:230px;font-size:20px;font-weight:500}
.stars{position:absolute;left:18px;top:262px;font-size:14px;letter-spacing:3px}
.stars small{font-family:"Poppins",sans-serif;font-size:11px;letter-spacing:0;color:var(--grey)}
.card .desc{position:absolute;left:18px;top:288px;width:200px;font-family:"Poppins",sans-serif;font-size:11px;line-height:19px;color:var(--grey)}
.card .btn{left:20px;top:334px;width:93px;height:33px;font-size:14px}
/* promo band */
.promo{left:0;top:1167px;width:1200px;height:587px;background:linear-gradient(100deg,#707070,#8e8e8e 45%,#5f6366 70%,#3f4a50)}
.pcard{top:60px;width:271px;height:414px;background:#eef1f4}
.pcard .media{position:absolute;left:26px;top:22px;width:219px;height:202px}
.pcard .price{position:absolute;left:30px;top:238px;color:var(--blue);font-size:25px;font-weight:600}
.pcard .name{position:absolute;left:30px;top:274px;font-size:21px;font-weight:500}
.pcard .stars{left:30px;top:310px;font-size:18px}
.pcard .btn{left:30px;top:343px;width:125px;height:36px;font-size:14px}
/* category */
.tabs{left:150px;top:1883px;width:900px;height:44px;background:var(--light);display:flex}
.tabs div{flex:1;display:flex;align-items:center;justify-content:center;color:var(--blue);font-weight:600;font-size:17px}
.tabs .on{background:var(--blue);color:var(--white)}
.info p{font-family:"Saira Semi Condensed",sans-serif;color:#333;text-align:justify}
/* discount */
.discount{left:0;top:2651px;width:1200px;height:368px;background:var(--band)}
.email{left:451px;top:2888px;width:488px;height:47px;background:var(--white);border:2px solid #fff;box-shadow:0 0 0 1px #d0d0d0}
/* testimonials */
.tcard{top:3158px;width:490px;height:266px;padding:36px 24px}
.tcard q{display:block;font-family:"Poppins",sans-serif;font-size:16px;line-height:25px;color:#444;quotes:"\201C" "\201D"}
.avatar{width:72px;height:72px;border-radius:50%;background:linear-gradient(#c9cdd3,#7e8896)}
/* footer */
.footer{left:0;top:3509px;width:1200px;height:362px;background:var(--black);color:var(--white)}
.fnav{left:0;top:184px;width:1200px;display:flex;justify-content:center;gap:34px;font-size:18px}
.pay{width:41px;height:26px;border-radius:3px}
</style>
</head>
<body>

<div class="abs topbar">Free Shipping On All Orders Over $50</div>

<header class="abs hero">
  <nav class="abs nav"><span class="active">Home</span><span>About</span><span>Shop</span><span>Category</span></nav>
  <div class="abs brand" style="left:542px;top:46px"><span class="dot"></span>Varlomatch</div>
  <div class="abs search">Search Product.......</div>
  <div class="abs iconbox" style="left:961px;top:25px">
    <svg width="14" height="14" viewBox="0 0 14 14"><circle cx="6" cy="6" r="4.5" fill="none" stroke="#000" stroke-width="2"/><line x1="9.5" y1="9.5" x2="13" y2="13" stroke="#000" stroke-width="2"/></svg>
  </div>
  <div class="abs iconbox" style="left:1009px;top:25px">
    <svg width="18" height="16" viewBox="0 0 18 16"><path d="M1 5h16l-2 10H3z" fill="none" stroke="#000" stroke-width="1.8"/><path d="M5 5l4-4 4 4" fill="none" stroke="#000" stroke-width="1.8"/></svg>
  </div>
  <div class="abs iconbox" style="left:1053px;top:25px">
    <svg width="14" height="14" viewBox="0 0 14 14"><circle cx="7" cy="4" r="3.3" fill="#000"/><path d="M1 14c0-4 3-6 6-6s6 2 6 6z" fill="#000"/></svg>
  </div>
  <div class="abs arrow" style="left:40px;top:251px">&larr;</div>
  <div class="abs arrow" style="left:1136px;top:251px">&rarr;</div>
  <div class="abs hero-img" role="img" aria-label="Pickleball paddle with two yellow balls"></div>
  <h1 class="abs"><span>Top Quality Material</span><br>And Accessories For Players</h1>
  <p class="abs">Lorem ipsum dolor sit amet, consectetur adipiscing elit, sed do eiusmod tempor incididunt ut labore et dolore magna aliqua.</p>
  <div class="btn" style="left:808px;top:338px;width:164px;height:37px;font-size:17px">Get Started Today!</div>
  <div class="btn" style="left:979px;top:338px;width:110px;height:37px;font-size:17px;background:var(--blue);color:var(--white)">Shop Now</div>
</header>

<h2 class="abs title" style="left:98px;top:650px">Best <span style="color:var(--blue)"></span>Sellers</h2>
<style>.bs-title span{color:var(--blue)}</style>
<div class="abs" style="left:1047px;top:660px;display:flex;gap:8px">
  <div class="arrow" style="background:#9cc9e6;color:#fff">&larr;</div>
  <div class="arrow" style="background:var(--blue);color:#fff">&rarr;</div>
</div>

<article class="abs card" style="left:99px">
  <div class="media" role="img" aria-label="Pair of pickleball rackets" style="background:linear-gradient(135deg,#fff 20%,#5a5f9a 50%,#fff 80%)"></div>
  <span class="tag" style="background:var(--blue)">NEW</span>
  <div class="price">$60.00</div><div class="name">Rackets</div>
  <div class="stars">★★★★★ <small>(4)</small></div>
  <p class="desc">Lorem ipsum dolor sit amet, consectetur elit, sed</p>
  <div class="btn">Shop Now</div>
</article>
<article class="abs card" style="left:354px">
  <div class="media" role="img" aria-label="Set of yellow pickleballs" style="background:radial-gradient(circle,#f2e94a 0%,#f6ef6a 35%,#fff 60%)"></div>
  <span class="tag" style="background:#e5202a">-17%</span>
  <div class="price">$60.00</div><div class="name">Set of Balls</div>
  <div class="stars">★★★★★ <small>(4)</small></div>
  <p class="desc">Lorem ipsum dolor sit amet, consectetur elit, sed</p>
  <div class="btn">Shop Now</div>
</article>
<article class="abs card focus" style="left:610px">
  <div class="media" role="img" aria-label="Portable pickleball net" style="background:linear-gradient(#6fc6ec,#4fb0e0)"></div>
  <span class="tag" style="background:var(--blue)">NEW</span>
  <div class="abs" style="left:198px;top:86px;display:flex;flex-direction:column;gap:12px">
    <div style="width:24px;height:24px;border-radius:50%;background:var(--yellow)"></div>
    <div style="width:24px;height:24px;border-radius:50%;background:var(--yellow)"></div>
  </div>
  <div class="price">$60.00</div><div class="name">NET</div>
  <div class="stars">★★★★★ <small>(4)</small></div>
  <p class="desc">Lorem ipsum dolor sit amet, consectetur elit, sed</p>
  <div class="btn">Shop Now</div>
</article>
<article class="abs card" style="left:865px">
  <div class="media" role="img" aria-label="Black overgrip rolls" style="background:radial-gradient(ellipse,#3a3a3a 0%,#777 30%,#fff 60%)"></div>
  <span class="tag" style="background:#e5202a">-17%</span>
  <div class="price">$60.00</div><div class="name">Overgrip</div>
  <div class="stars">★★★★★ <small>(4)</small></div>
  <p class="desc">Lorem ipsum dolor sit amet, consectetur elit, sed</p>
  <div class="btn">Shop Now</div>
</article>

<section class="abs promo" role="img" aria-label="Player hitting a pickleball on an indoor court">
  <div class="abs pcard" style="left:52px">
    <div class="media" role="img" aria-label="Black player bag" style="background:radial-gradient(ellipse,#2a2a2a 0%,#555 40%,#eef1f4 65%)"></div>
    <div class="price">From $60.00</div><div class="name">Player Bag</div>
    <div class="stars">☆☆☆☆☆</div>
    <div class="btn">BUY NOW</div>
  </div>
  <div class="abs pcard" style="left:344px">
    <div class="media" role="img" aria-label="Water bottles" style="background:linear-gradient(90deg,#eef1f4 20%,#fff 25%,#9a9a9a 40%,#d5d5d5 60%,#fff 75%,#eef1f4 80%)"></div>
    <div class="price">From $30.00</div><div class="name">Water Bottle</div>
    <div class="stars">☆☆☆☆☆</div>
    <div class="btn">BUY NOW</div>
  </div>
</section>

<h2 class="abs title" style="left:0;width:1200px;text-align:center;top:1813px"><span>About</span> The Category</h2>
<div class="abs tabs">
  <div class="on">Rackets</div><div>Set of balls</div><div>Net</div><div>Lines</div><div>Overgrip</div><div>Water Bottle</div><div>Player Bag</div>
</div>

<div class="abs" role="img" aria-label="Blue pickleball racket with orange balls" style="left:111px;top:1990px;width:443px;height:463px;background:radial-gradient(ellipse,#3f7fe0 0%,#6fa0e8 30%,#e9eef0 60%)"></div>
<div class="abs" style="left:111px;top:2465px;display:flex;gap:8px">
  <div role="img" aria-label="Yellow balls" style="width:83px;height:88px;background:linear-gradient(#e8c93a,#3d5ea8)"></div>
  <div role="img" aria-label="Paddles on blue" style="width:83px;height:88px;background:linear-gradient(#3f7fd8,#e8a83a)"></div>
  <div role="img" aria-label="Players on court" style="width:83px;height:88px;background:linear-gradient(#9aa3a0,#5d6a62)"></div>
  <div role="img" aria-label="Pickleball event banner" style="width:83px;height:88px;background:linear-gradient(#7b7fa8,#3d4a8a)"></div>
  <div role="img" aria-label="Video of a player" style="width:83px;height:88px;background:linear-gradient(#9ab5d8,#3a4f7a)"></div>
</div>

<div class="abs info" style="left:607px;top:2036px;width:490px">
  <h3 style="font-size:31px;font-weight:600">Rackets</h3>
  <div style="font-size:35px;font-weight:700;color:var(--blue);margin-top:4px">$59.99</div>
  <p style="font-size:17px;line-height:29px;margin-top:6px">Lorem ipsum dolor sit amet, consectetur adipiscing elit, sed do eiusmod tempor incididunt ut labore et dolore magna aliqua. Ut enim ad minim veniam, quis nostrud exercitation ullamco laboris nisi ut aliquip ex ea commodo consequat.</p>
  <p style="font-size:14px;line-height:23px;margin-top:8px">Lorem ipsum dolor sit amet, consectetur adipiscing elit, sed do eiusmod tempor incididunt ut labore et dolore magna aliqua.</p>
  <p style="font-size:14px;line-height:25px;margin-top:10px">Sed ut perspiciatis unde omnis iste natus error sit voluptatem accusantium doloremque laudantium, totam rem aperiam, eaque ipsa quae ab illo inventore veritatis et quasi architecto beatae vitae dicta sunt explicabo. Nemo enim</p>
</div>
<div class="btn" style="left:607px;top:2415px;width:136px;height:36px;font-size:18px">Add Cart Now</div>

<section class="abs discount">
  <div class="abs" style="left:0;top:0;width:330px;height:368px;background:linear-gradient(135deg,#b9cc8d 0%,#a9c07a 40%,var(--band) 40%)"></div>
  <div class="abs" role="img" aria-label="Paddles, balls and player bag" style="left:55px;top:30px;width:310px;height:338px;border-radius:30% 30% 10% 10%;background:linear-gradient(160deg,#2c4a96 0%,#1f2f62 45%,#2a2a2a 70%)"></div>
  <h2 class="abs" style="left:448px;top:68px;font-size:44px;font-weight:600;color:var(--white)">UP TO 50% DISCOUNT</h2>
  <p class="abs" style="left:448px;top:140px;width:642px;color:var(--white);font-size:17px;line-height:29px;text-align:justify">Sed ut perspiciatis unde omnis iste natus error sit voluptatem accusantium doloremque laudantium, totam rem aperiam, eaque ipsa quae ab illo inventore veritatis et quasi architecto beatae vitae dicta sunt explicabo.</p>
</section>
<div class="abs email">
  <span class="abs" style="left:12px;top:9px;font-size:18px">Enter Email</span>
  <div class="btn" style="left:396px;top:4px;width:86px;height:35px;font-size:18px">Submit</div>
</div>

<h2 class="abs title" style="left:98px;top:3085px;color:var(--blue)">Testimonials</h2>
<div class="abs tcard" style="left:90px;box-shadow:0 0 9px rgba(0,0,0,.14)">
  <q>Lorem ipsum dolor sit amet, consectetur adipiscing elit, sed do eiusmod tempor incididunt ut labore et dolore magna aliqua. Ut enim ad minim veniam, quis nostrud exercitation ullamco laboris nisi ut aliquip commodo consequat</q>
  <div class="abs avatar" role="img" aria-label="Customer portrait" style="left:30px;top:164px"></div>
  <div class="abs" style="left:120px;top:178px;font-size:18px;font-weight:600;letter-spacing:2px">TOM</div>
  <div class="abs" style="left:120px;top:206px;font-family:Poppins,sans-serif;font-size:16px;color:#444">Lorem ipsum</div>
</div>
<div class="abs tcard" style="left:622px">
  <q>Lorem ipsum dolor sit amet, consectetur adipiscing elit, sed do eiusmod tempor incididunt ut labore et dolore magna aliqua. Ut enim ad minim veniam, quis nostrud exercitation ullamco laboris nisi ut aliquip commodo consequat</q>
  <div class="abs avatar" role="img" aria-label="Customer portrait" style="left:28px;top:164px"></div>
  <div class="abs" style="left:120px;top:178px;font-size:18px;font-weight:600;letter-spacing:2px">JHON</div>
  <div class="abs" style="left:120px;top:206px;font-family:Poppins,sans-serif;font-size:16px;color:#444">Lorem ipsum</div>
</div>

<footer class="abs footer">
  <div class="abs brand" style="left:0;width:1200px;justify-content:center;top:88px;font-size:30px"><span class="dot" style="width:28px;height:28px"></span>Varlomatch</div>
  <nav class="abs fnav"><span>Home</span><span>|</span><span>About</span><span>|</span><span>Shop</span><span>|</span><span>Category</span></nav>
  <div class="abs" style="left:458px;top:237px;display:flex;gap:6px">
    <div class="pay" style="background:#e0e0e0"></div>
    <div class="pay" style="background:#f2f2f2"></div>
    <div class="pay" style="background:#ffffff"></div>
    <div class="pay" style="background:#f4f4f4"></div>
    <div class="pay" style="background:#2e77bb"></div>
    <div class="pay" style="background:#d9d9d9"></div>
  </div>
  <div class="abs" style="left:0;width:1200px;text-align:center;top:320px;font-size:14px">Copyright © 2023 Varlomatch | All Rights Reserved. Privacy policy</div>
</footer>

</body>
</html>
```